Harbourline Electrical Solutions

On one side. LOGO (underneath:) Commercial Industrial Residential

- NAME & CONTACT DETAILS

Marcus T. Hollings
Project Manager

(Cell icon) (441) 555-0187
(Email icon) hlelectricalsolutions@mailvento.com
(Facebook & Instagram icons )@hlelectricalsolutions

Other side: LOGO - underneath ELECTRICAL CONSTRUCTION & MAINTENANCE . LED LIGHTING & AUTOMATION . LIFE SAFETY SYSTEMS (FIRE ALARM / SECURITY) . DATA & COMMUNICATION

```html
<!DOCTYPE html>
<html lang="en">
<head>
<meta charset="utf-8">
<title>Harbourline Electrical Solutions – Business Card</title>
<link href="https://fonts.googleapis.com/css2?family=Montserrat:wght@400;500;600;700&display=swap" rel="stylesheet">
<style>
  :root{
    --backdrop:#1f1f21;
    --teal:#10576d;
    --white:#ffffff;
    --ink:#3c3c3c;
    --grey:#5a5a5a;
  }
  html,body{margin:0;padding:0;width:1200px;height:1200px;overflow:hidden;background:var(--backdrop);}
  body{position:relative;font-family:"Montserrat",sans-serif;}

  .card{position:absolute;overflow:hidden;}
  .card--services{left:292px;top:220px;width:599px;height:359px;background:var(--teal);color:var(--white);}
  .card--contact{left:284px;top:629px;width:614px;height:368px;background:var(--white);}

  .services{position:absolute;left:50px;top:148px;margin:0;padding:0;list-style:none;}
  .services li{font-size:11.4px;font-weight:500;line-height:18px;letter-spacing:.1px;white-space:nowrap;}
  .services li::before{content:"";display:inline-block;width:4px;height:4px;border-radius:50%;background:var(--white);margin:0 7px 2px 0;vertical-align:middle;}

  .brand{position:absolute;right:40px;top:40px;text-align:right;}
  .brand__row{display:flex;align-items:center;justify-content:flex-end;gap:8px;}
  .brand__mark{width:12px;height:12px;flex:none;}
  .brand__name{margin:0;font-size:13px;font-weight:600;letter-spacing:1.2px;text-transform:uppercase;white-space:nowrap;}
  .card--services .brand__mark{background:var(--white);}
  .card--services .brand__name{color:var(--white);}
  .card--contact .brand__mark{background:var(--teal);}
  .card--contact .brand__name{color:var(--teal);}
  .brand__tagline{margin:6px 0 0;font-size:10px;font-weight:500;letter-spacing:1px;color:var(--grey);text-transform:uppercase;}

  .person{position:absolute;left:41px;top:240px;}
  .person__name{margin:0;font-size:18.5px;font-weight:700;color:var(--teal);letter-spacing:.2px;line-height:22px;}
  .person__role{margin:0;font-size:12.5px;color:var(--ink);line-height:16px;}

  .contacts{position:absolute;left:40px;top:289px;margin:0;padding:0 0 0 7px;list-style:none;border-left:1px solid var(--teal);}
  .contacts li{display:flex;align-items:center;gap:5px;font-size:12.4px;font-weight:500;color:var(--ink);line-height:19.5px;}
  .contacts svg{width:12px;height:12px;flex:none;}
</style>
</head>
<body>

<section class="card card--services">
  <div class="brand">
    <div class="brand__row">
      <span class="brand__mark"></span>
      <p class="brand__name">Harbourline Electrical Solutions</p>
    </div>
  </div>
  <ul class="services">
    <li>ELECTRICAL CONSTRUCTION &amp; MAINTENANCE</li>
    <li>LED LIGHTING &amp; AUTOMATION</li>
    <li>LIFE SAFETY SYSTEMS (FIRE ALARM / SECURITY)</li>
    <li>DATA &amp; COMMUNICATION</li>
  </ul>
</section>

<section class="card card--contact">
  <div class="brand">
    <div class="brand__row">
      <span class="brand__mark"></span>
      <p class="brand__name">Harbourline Electrical Solutions</p>
    </div>
    <p class="brand__tagline">Commercial · Industrial · Residential</p>
  </div>
  <div class="person">
    <h1 class="person__name">MARCUS T. HOLLINGS</h1>
    <p class="person__role">Project Manager</p>
  </div>
  <ul class="contacts">
    <li>
      <svg viewBox="0 0 12 12" aria-hidden="true"><circle cx="6" cy="6" r="5.4" fill="none" stroke="#10576d" stroke-width=".9"/><path d="M4.2 3.3l1 1-.6.7c.4.8 1 1.4 1.8 1.8l.7-.6 1 1-.8.9C5.4 7.8 4 6.4 3.4 4.1z" fill="#10576d"/></svg>
      (441) 555-0187
    </li>
    <li>
      <svg viewBox="0 0 12 12" aria-hidden="true"><circle cx="6" cy="6" r="5.4" fill="none" stroke="#10576d" stroke-width=".9"/><rect x="3.4" y="4.2" width="5.2" height="3.6" fill="none" stroke="#10576d" stroke-width=".8"/><path d="M3.4 4.2L6 6.2l2.6-2" fill="none" stroke="#10576d" stroke-width=".8"/></svg>
      hlelectricalsolutions@mailvento.com
    </li>
    <li>
      <svg viewBox="0 0 12 12" aria-hidden="true"><circle cx="6" cy="6" r="5.4" fill="none" stroke="#10576d" stroke-width=".9"/></svg>
      <svg viewBox="0 0 12 12" aria-hidden="true"><circle cx="6" cy="6" r="5.4" fill="none" stroke="#10576d" stroke-width=".9"/></svg>
      @hlelectricalsolutions
    </li>
  </ul>
</section>

</body>
</html>
```